Creation of a Valterna Flyer design

As part of the cr% 26 # 233; ation of our soci% 26 # 233; t% 26 # 233 ;, we wish to cr% 26 # 233; er a flyer pr% 26 # 233; feeling our diff% 26 # 233; annuities% 26 # 233; s business advisory services% 26 # 233; foreign% 26 # 232; res who wish to develop their activities% 26 # 233; s in Switzerland. We want a double-sided flyer that presents% 26 # 233; society% 26 # 233; t% 26 # 233; d% 26 # 39; a c% 26 # 244; t% 26 # 233; and who presents% 26 # 233; benefits of the other. We have d% 26 # 233; j% 26 # 224; made a very basic provisional flyer to be able to present our activities. We put it to you as an example.

Target Market(s)

European companies% 26 # 233; internal% 26 # 233; res% 26 # 233; es by the market% 26 # 233; Swiss

Industry/Entity Type

Business Consultant

Colors

Designer to choose colors to be used in the design.

Requirements
Must have
• Company name and contact details
A field to detail the services
Nice to have
• Some% 26 # 233; l% 26 # 233; elements that recall Switzerland and some% 26 # 233; l% 26 # 233; elements that recall c% 26 # 244; t% 26 # 233; % 26quot; business% 26quot;

```html
<!DOCTYPE html>
<html lang="en">
<head>
<meta charset="utf-8">
<title>Valterna Flyer</title>
<link href="https://fonts.googleapis.com/css2?family=Roboto+Condensed:wght@300;400&family=Questrial&display=swap" rel="stylesheet">
<style>
  :root {
    --backdrop: #6b6c6f;
    --paper: #f1f2f3;
    --paper-shade: #d9dadc;
    --brand-blue: #3a6db5;
    --deep-blue: #2f5aa8;
    --violet: #4a3a9a;
    --purple: #6b3a96;
    --ink: #2a2a2e;
    --sky: #6f9fd8;
    --snow: #dfe6ee;
    --lake: #3fb3c4;
  }
  * { box-sizing: border-box; margin: 0; padding: 0; }
  html, body { width: 1200px; height: 1200px; overflow: hidden; }
  body { background: var(--backdrop); position: relative; }

  .flyer {
    position: absolute;
    left: 136px; top: 0;
    width: 904px; height: 1170px;
    transform: scale(1.0256);
    transform-origin: top left;
    background: linear-gradient(90deg, var(--paper) 0%, var(--paper) 55%, var(--paper-shade) 100%);
    overflow: hidden;
  }
  .flyer-art { position: absolute; inset: 0; }

  .brand {
    position: absolute; right: 40px; top: 40px;
    display: flex; flex-direction: column; align-items: center; gap: 14px;
  }
  .brand-mark { width: 52px; height: 48px; background: #e9edf3; border-radius: 9px; }
  .brand-name {
    font-family: "Questrial", sans-serif; color: #ffffff;
    font-size: 34px; letter-spacing: 3px; line-height: 1;
  }

  .intro {
    position: absolute; left: 48px; top: 436px; width: 402px;
    font-family: "Roboto Condensed", sans-serif; font-weight: 300;
    font-size: 24.5px; line-height: 30px; color: var(--ink);
    text-align: justify;
  }
  .headline {
    position: absolute; left: 503px; top: 512px; width: 380px;
    font-family: "Questrial", sans-serif; color: var(--brand-blue);
    font-size: 35px; line-height: 42px;
  }
  .details {
    position: absolute; left: 48px; top: 728px; width: 808px;
    font-family: "Roboto Condensed", sans-serif; font-weight: 300;
    font-size: 19px; line-height: 23.4px; color: var(--ink);
    text-align: justify;
  }
  .details p + p { margin-top: 23px; }
  .footnote {
    position: absolute; left: 48px; top: 1000px;
    font-family: "Roboto Condensed", sans-serif; font-weight: 300;
    font-size: 13.5px; color: var(--ink);
  }
</style>
</head>
<body>
<main class="flyer">
  <svg class="flyer-art" viewBox="0 0 904 1170" width="904" height="1170" aria-hidden="false">
    <defs>
      <linearGradient id="alpine-sky" x1="0" y1="0" x2="0" y2="1">
        <stop offset="0" stop-color="#3f78c9"/>
        <stop offset="0.45" stop-color="var(--sky)"/>
        <stop offset="0.75" stop-color="var(--snow)"/>
        <stop offset="1" stop-color="#8a7a6a"/>
      </linearGradient>
      <linearGradient id="corner-blue" x1="0" y1="0" x2="1" y2="1">
        <stop offset="0" stop-color="#3b6fbe"/>
        <stop offset="1" stop-color="var(--deep-blue)"/>
      </linearGradient>
      <linearGradient id="tile-fill" x1="0" y1="0" x2="1" y2="1">
        <stop offset="0" stop-color="#3f4fa8"/>
        <stop offset="1" stop-color="var(--purple)"/>
      </linearGradient>
      <linearGradient id="lakeside" x1="0" y1="0" x2="0" y2="1">
        <stop offset="0" stop-color="#9cc3e6"/>
        <stop offset="0.45" stop-color="#b98a68"/>
        <stop offset="0.75" stop-color="#6f8a5a"/>
        <stop offset="1" stop-color="var(--lake)"/>
      </linearGradient>
      <linearGradient id="band-violet" x1="0" y1="0" x2="1" y2="0">
        <stop offset="0" stop-color="var(--violet)"/>
        <stop offset="1" stop-color="var(--purple)"/>
      </linearGradient>
    </defs>

    <!-- alpine header -->
    <path role="img" aria-label="Photo of a snow-covered Alpine peak under a blue sky"
          d="M0,0 H904 V505 C560,350 250,355 0,398 Z" fill="url(#alpine-sky)"/>
    <!-- violet sweep across header -->
    <path d="M300,370 C520,360 740,420 904,478 V505 C740,440 520,380 300,370 Z" fill="url(#band-violet)" opacity="0.85"/>
    <!-- blue edge of header -->
    <path d="M0,392 C250,350 560,345 904,500 V512 C560,358 250,362 0,404 Z" fill="var(--brand-blue)"/>

    <!-- top-right brand panel -->
    <path d="M470,0 H904 V240 C760,225 580,130 470,0 Z" fill="url(#corner-blue)"/>
    <path d="M425,0 H470 C580,130 760,225 904,240 V278 C740,240 560,140 425,0 Z" fill="url(#band-violet)"/>

    <!-- central tile -->
    <rect x="505" y="315" width="190" height="183" rx="32" fill="url(#tile-fill)"/>

    <!-- lakeside footer -->
    <path d="M110,1170 C320,1030 620,960 904,995 V1170 Z" fill="url(#band-violet)"/>
    <path d="M150,1170 C340,1050 600,985 904,1010 V1170 Z" fill="#ffffff"/>
    <path role="img" aria-label="Photo of a lakeside castle village with turquoise water"
          d="M210,1170 C380,1070 620,1010 904,1022 V1170 Z" fill="url(#lakeside)"/>
  </svg>

  <div class="brand">
    <span class="brand-mark"></span>
    <span class="brand-name">VALTERNA</span>
  </div>

  <p class="intro">The potential of the Swill market offers many business opportunities to foreign companies, however there are some tariff and non-tariff barriers to cope with, such as its strong requirements in terms of quality and innovation, cultural and linguistic differences, specific rules applied to certain products or services.</p>

  <h1 class="headline">Valterna is there to support you in your administrative and strategic procedures!</h1>

  <div class="details">
    <p>Valterna strives to deepen the understanding of your business and acts as your local partner. We assist you in defining together all the services that best meet your needs.</p>
    <p>Our consulting skills are focused on high added value sectors, such as food and beverages, fashion &amp; lifestyle, products and services for leading industries (pharmaceutical, chemical, precision mechanics) or sustainable solutions (renewable energies, recyclable materials).</p>
    <p>From our office in Neuchate* and with our language knowledges, we are able to cover the whole of Switzerland. Having many years of experience in economic promotion and business managment, we are familiar with the Swiss trade and foreign companies wishing to export to Switzerland.</p>
  </div>

  <p class="footnote">*as of August 2020, we will open an office in Zurich as well</p>
</main>
</body>
</html>
```